Lifecoach needs website design based on a standard Wordpress theme

I need a website for my new lifecoaching business that can be easily implemented in Wordpress, it needs to be compatible with a standard Wordpress theme. So I can place the pictures, texts etc. in a standard theme of Wordpress.

I want the design to be a very good feeling and playfull one, based on my logo.

Target Market(s)

I will coach people to reach their goals and dreams in life.

Industry/Entity Type

Business

Requirements
Must have
• Can be easy implemented in Wordpress.
Nice to have
• Photo's of nature are nice.

```html
<!DOCTYPE html>
<html lang="en">
<head>
<meta charset="utf-8">
<title>Ruben ter Haar Lifecoach</title>
<link rel="stylesheet" href="https://fonts.googleapis.com/css2?family=Open+Sans:wght@400;600&display=swap">
<style>
:root{
  --brand:#0d5c92;
  --brand-light:#1a9bd8;
  --nav-top:#0b6aab;
  --nav-bottom:#064a7c;
  --nav-active:#17a6e2;
  --nav-line:#04395f;
  --text:#7a7a7a;
  --text-dark:#222;
  --rule:#dcdcdc;
  --footer:#2f2f2f;
  --footer-text:#bdbdbd;
  --white:#fff;
}
*{box-sizing:border-box;margin:0;padding:0}
html,body{width:1030px;height:1200px;overflow:hidden;background:var(--white)}
body{font-family:"Open Sans",Arial,sans-serif;color:var(--text);position:relative}
.abs{position:absolute}

/* header */
.brand{left:87px;top:10px;display:flex;align-items:center;gap:10px}
.brand-mark{width:76px;height:76px;border-radius:50%;border:4px solid var(--brand-light)}
.brand-name{font-size:22px;font-weight:600;color:var(--brand);letter-spacing:1px;line-height:1.15;width:220px}
.call{right:119px;top:30px;text-align:right}
.call-label{font-size:14px;color:#666}
.call-number{font-size:19px;font-weight:600;color:var(--brand);line-height:1.1}
.call-icon{left:916px;top:38px}

/* nav */
.nav{left:0;top:105px;width:1030px;height:45px;background:linear-gradient(var(--nav-top),var(--nav-bottom))}
.nav-list{position:absolute;left:87px;top:0;display:flex;list-style:none;height:45px;border-left:1px solid var(--nav-line)}
.nav-list li{height:45px;display:flex;align-items:center;justify-content:center;color:var(--white);font-size:13px;font-weight:600;border-right:1px solid var(--nav-line)}
.nav-list li.active{background:var(--nav-active)}
.search{left:798px;top:114px;width:146px;height:27px;background:var(--white);border-radius:3px;font-size:11px;color:#aaa;padding:6px 8px}
.search-icon{position:absolute;right:6px;top:5px}
.search::after{content:"";position:absolute;right:27px;top:4px;width:1px;height:19px;background:#ddd}

/* hero */
.hero{left:0;top:150px;width:1030px;height:395px;background:linear-gradient(200deg,#cfe6f2 0%,#8fd0e0 35%,#7fb83a 72%,#d2c61c 100%)}
.hero-arrow{left:86px;top:332px;width:30px;height:30px;border-radius:50%;background:rgba(255,255,255,.9)}
.caption{left:544px;top:284px;width:400px;height:127px;background:rgba(80,88,80,.62);border-radius:3px;padding:14px 14px 0 14px;color:var(--white)}
.caption h1{font-size:27px;font-weight:600;line-height:1.15;margin-bottom:8px}
.caption p{font-size:12.3px;font-weight:600;line-height:20px}

/* content */
.section-title{font-size:20px;font-weight:600;color:var(--brand);white-space:nowrap}
.welcome-photo{left:86px;top:610px;width:277px;height:160px;background:linear-gradient(180deg,#c9b27a 0%,#f3d76e 45%,#b8a27a 75%,#8e8470 100%)}
.body-text{font-size:11.6px;line-height:18px;color:var(--text)}
.btn{left:86px;top:884px;width:77px;height:30px;border-radius:3px;background:linear-gradient(#7b7b7b,#575757);color:var(--white);font-size:12px;display:flex;align-items:center;justify-content:center}
.divider-v{left:381px;top:583px;width:1px;height:332px;background:var(--rule)}
.service-photo{left:400px;width:193px;height:141px}
.service-photo.personal{top:610px;background:linear-gradient(135deg,#d9d3cc,#b89c86 50%,#c85a4e)}
.service-photo.professional{top:771px;background:linear-gradient(180deg,#e4eef6,#b9c9d6 60%,#8e8372)}
.service-title{left:607px;font-size:15.5px;color:var(--brand-light)}
.service-text{left:607px;width:340px}
.read-more{left:608px;font-size:11.5px;font-weight:600;color:var(--text-dark)}

/* testimonials */
.divider-h{left:86px;top:962px;width:859px;height:1px;background:var(--rule)}
.testimonials{left:0;top:985px;width:1030px;text-align:center}
.testimonials h2{font-size:17px;font-weight:600;color:var(--brand);margin-bottom:10px}
.quote{font-size:15px;line-height:20px;color:#6d6d6d}
.client{font-size:14.5px;color:var(--brand);margin-top:7px}
.t-arrow{top:1032px}

/* footer */
.footer{left:0;top:1112px;width:1030px;height:88px;background:var(--footer)}
.footer-links{position:absolute;left:87px;top:21px;font-size:11.5px;color:var(--footer-text);word-spacing:2px}
.footer-links span{margin:0 9px;color:#999}
.copyright{position:absolute;left:87px;top:52px;font-size:11.5px;color:var(--footer-text)}
.social{position:absolute;left:833px;top:33px;display:flex;gap:9px}
.social i{display:flex;align-items:center;justify-content:center;width:21px;height:21px;border-radius:50%;background:#6e6e6e}
</style>
</head>
<body>

<header>
  <div class="brand abs">
    <div class="brand-mark"></div>
    <div class="brand-name">RUBEN TER HAAR LIFECOACH</div>
  </div>
  <div class="call abs">
    <div class="call-label">Call us</div>
    <div class="call-number">555 014 2390</div>
  </div>
  <svg class="call-icon abs" width="28" height="24" viewBox="0 0 28 24">
    <path d="M4 3c2-1 3-1 4 1l2 4c0 1-1 2-2 3 1 3 3 5 6 6 1-1 2-2 3-2l4 2c2 1 2 2 1 4-1 2-3 3-5 2C10 21 5 16 2 9 1 7 2 4 4 3z" fill="#666"/>
    <path d="M19 4a6 6 0 0 1 5 5M19 8a3 3 0 0 1 2 2" stroke="#888" stroke-width="1.5" fill="none"/>
  </svg>
</header>

<nav class="nav abs">
  <ul class="nav-list">
    <li class="active" style="width:82px">HOME</li>
    <li style="width:113px">ABOUT US</li>
    <li style="width:104px">SERVICES</li>
    <li style="width:84px">BLOG</li>
    <li style="width:139px">TESTIMONIALS</li>
    <li style="width:124px">CONTACT US</li>
  </ul>
</nav>
<div class="search abs">Search
  <svg class="search-icon" width="16" height="16" viewBox="0 0 16 16"><circle cx="6.5" cy="6.5" r="5" stroke="#888" stroke-width="2" fill="none"/><path d="M10 10l5 5" stroke="#888" stroke-width="2.2"/></svg>
</div>

<section class="hero abs" role="img" aria-label="Nature photo: a butterfly resting on a yellow flower against a soft blue and green background"></section>
<div class="hero-arrow abs">
  <svg width="30" height="30" viewBox="0 0 30 30"><path d="M17 10l-5 5 5 5" stroke="#999" stroke-width="1.5" fill="none"/></svg>
</div>
<div class="caption abs">
  <h1>Maecenas molestie mollis</h1>
  <p>Aliquam tempus, nisi in venenatis feugiat, eros ligula fermentum eros, vitae ultrices ligula nibh ac dolor. Fusce quis mauris at urna laoreet gravida non nec sapien.</p>
</div>

<main>
  <h2 class="section-title abs" style="left:86px;top:577px;letter-spacing:-.3px">Welcome to RUBEN TER HAAR</h2>
  <div class="welcome-photo abs" role="img" aria-label="Silhouette of a person on a mountain top raising an arm against a sunrise"></div>
  <p class="body-text abs" style="left:87px;top:781px;width:276px">Nam ut nisl tempus odio iaculis sodales sit amet lacinia enim. Maecenas posuere, lacus tincidunt rhoncus congue, mi ante fringilla magna, et tristique massa quam rutrum justo. Maecenas lobortis arcu non adipiscing pulvinar.</p>
  <div class="btn abs">View more</div>

  <div class="divider-v abs"></div>

  <h2 class="section-title abs" style="left:399px;top:577px">Our Services</h2>

  <div class="service-photo personal abs" role="img" aria-label="Portrait photo of a smiling man in a checked shirt"></div>
  <h3 class="service-title abs" style="top:613px;font-weight:400">Personal Empowerment</h3>
  <p class="service-text body-text abs" style="top:641px">Nam ut nisl tempus odio iaculis sodales sit amet lacinia enim. Maecenas posuere, lacus tincidunt rhoncus congue, mi ante fringilla magna, et tristique massa quam rutrum justo. Maecenas lobortis arcu non adipiscing pulvinar.</p>
  <div class="read-more abs" style="top:727px">READ MORE</div>

  <div class="service-photo professional abs" role="img" aria-label="Photo of a businessman with a laptop cheering outdoors"></div>
  <h3 class="service-title abs" style="top:774px;font-weight:400">Professional Empowerment</h3>
  <p class="service-text body-text abs" style="top:802px">Nam ut nisl tempus odio iaculis sodales sit amet lacinia enim. Maecenas posuere, lacus tincidunt rhoncus congue, mi ante fringilla magna, et tristique massa quam rutrum justo. Maecenas lobortis arcu non adipiscing pulvinar.</p>
  <div class="read-more abs" style="top:888px">READ MORE</div>

  <div class="divider-h abs"></div>

  <section class="testimonials abs">
    <h2>Testimonials</h2>
    <p class="quote">Fusce quis mauris at urna laoreet gravida non nec sapien. Duis tincidunt est quis lacinia congue.<br>Quisque libero odio, lobortis a justo et, tempor commodo eros.</p>
    <p class="client">Client name, City</p>
  </section>
  <svg class="t-arrow abs" style="left:86px" width="16" height="28" viewBox="0 0 16 28"><path d="M14 2L3 14l11 12" stroke="#aaa" stroke-width="2" fill="none"/></svg>
  <svg class="t-arrow abs" style="left:929px" width="16" height="28" viewBox="0 0 16 28"><path d="M2 2l11 12L2 26" stroke="#aaa" stroke-width="2" fill="none"/></svg>
</main>

<footer class="footer abs">
  <div class="footer-links">Home<span>|</span>About us<span>|</span>Services<span>|</span>Blog<span>|</span>Testimonials<span>|</span>Contact us</div>
  <div class="copyright">Copyright &copy; 2014 &nbsp;RUBEN TER HAAR. &nbsp;All rights reserved.</div>
  <div class="social">
    <i></i><i></i><i></i>
    <i><svg width="12" height="9" viewBox="0 0 12 9"><rect x=".5" y=".5" width="11" height="8" fill="none" stroke="#2f2f2f"/><path d="M.5 .5l5.5 4.5 5.5-4.5" fill="none" stroke="#2f2f2f"/></svg></i>
  </div>
</footer>

</body>
</html>
```